Business cards for KORU Real Estate Holdings LLC

We need a cool, original business card design for a company based in the Washington DC metropolitan area. We are a new energetic and passionate Real Estate Investing Company that invests in all types of real estate; commercial, residential, industrial etc.

Our company color is Red since it reflects action, energy and speed; it is assertive confident, energizing, exciting, powerful, passionate and determined. So we would like business card communicate those qualities to the audience.

Our audiences are investors that want to invest with us, real estate sellers, buyers, and tenants who lease from us.

Our logo is attached

```html
<!DOCTYPE html>
<html lang="en">
<head>
<meta charset="utf-8">
<title>KORU Real Estate Holdings LLC — Business Cards</title>
<link rel="stylesheet" href="https://fonts.googleapis.com/css2?family=Roboto:wght@400;700&display=swap">
<style>
  :root{
    --bg:#d6d6d6;
    --card:#ffffff;
    --red:#f50a0a;
    --dark:#3b3b3d;
    --grey:#a7a8ac;
    --ink:#231f20;
  }
  html,body{margin:0;padding:0;overflow:hidden;}
  body{width:1200px;height:960px;background:var(--bg);position:relative;font-family:"Roboto",Arial,sans-serif;color:var(--ink);}
  .card{position:absolute;background:var(--card);overflow:hidden;}
  .card--front{left:112px;top:52px;width:728px;height:416px;}
  .card--back{left:377px;top:492px;width:679px;height:391px;}
  .tile-band{position:absolute;top:0;bottom:0;
    background:linear-gradient(180deg,var(--red) 0%,var(--dark) 22%,var(--grey) 40%,var(--red) 58%,var(--dark) 78%,var(--grey) 100%);}
  .card--front .tile-band--left{left:0;width:137px;}
  .card--front .tile-band--right{right:0;width:138px;}
  .card--back .tile-band--left{left:0;width:128px;}
  .card--back .tile-band--right{right:0;width:32px;}
  .brand{position:absolute;display:flex;align-items:center;gap:14px;}
  .brand__mark{background:var(--red);flex:none;}
  .brand__name{color:var(--ink);line-height:1.05;white-space:nowrap;}
  .brand__name span{display:block;}
  .brand__big{font-weight:700;}
  .brand__small{font-weight:400;}
  .card--front .brand{left:168px;top:176px;}
  .card--front .brand__mark{width:56px;height:56px;}
  .card--front .brand__big{font-size:74px;letter-spacing:2px;}
  .card--front .brand__small{font-size:20px;}
  .card--back .brand{left:148px;top:152px;gap:12px;}
  .card--back .brand__mark{width:38px;height:38px;}
  .card--back .brand__big{font-size:46px;letter-spacing:2px;}
  .card--back .brand__small{font-size:14px;}
  .contact{position:absolute;left:439px;top:122px;margin:0;padding:0;list-style:none;font-size:13px;}
  .contact li{display:flex;align-items:center;gap:10px;height:25px;}
  .contact svg{width:14px;height:14px;flex:none;}
</style>
</head>
<body>
  <section class="card card--front">
    <div class="tile-band tile-band--left" role="img" aria-label="Mosaic of red, charcoal and grey square tiles"></div>
    <div class="tile-band tile-band--right" role="img" aria-label="Mosaic of red, charcoal and grey square tiles"></div>
    <div class="brand">
      <div class="brand__mark"></div>
      <div class="brand__name"><span class="brand__big">KORU</span><span class="brand__small">REAL ESTATE HOLDINGS LLC</span></div>
    </div>
  </section>

  <section class="card card--back">
    <div class="tile-band tile-band--left" role="img" aria-label="Mosaic of red, charcoal and grey square tiles"></div>
    <div class="tile-band tile-band--right" role="img" aria-label="Column of red, charcoal and grey square tiles"></div>
    <div class="brand">
      <div class="brand__mark"></div>
      <div class="brand__name"><span class="brand__big">KORU</span><span class="brand__small">REAL ESTATE HOLDINGS LLC</span></div>
    </div>
    <ul class="contact">
      <li><svg viewBox="0 0 14 14"><rect x="3" y="0.5" width="8" height="13" rx="1.5" fill="var(--red)"/><rect x="4.5" y="2.5" width="5" height="7" fill="#fff"/></svg>55 0172 3384</li>
      <li><svg viewBox="0 0 14 14"><path d="M1 5c0-2 3-3 6-3s6 1 6 3v1H10V4.5H4V6H1z" fill="var(--ink)"/><rect x="2" y="7" width="10" height="6" rx="1" fill="var(--ink)"/><circle cx="7" cy="10" r="1.5" fill="#fff"/></svg>44 0261 9057</li>
      <li><svg viewBox="0 0 14 14"><rect x="1" y="3" width="12" height="8" fill="var(--ink)"/><path d="M1 3l6 5 6-5" fill="none" stroke="#fff" stroke-width="1"/></svg>info@koruholdings.com</li>
      <li><svg viewBox="0 0 14 14" fill="none" stroke="var(--ink)" stroke-width="1"><circle cx="7" cy="7" r="6"/><ellipse cx="7" cy="7" rx="2.6" ry="6"/><path d="M1 7h12M2 4h10M2 10h10"/></svg>www.koruholdings.com</li>
      <li><svg viewBox="0 0 14 14"><path d="M7 13C4 9 2.5 7 2.5 5a4.5 4.5 0 019 0c0 2-1.5 4-4.5 8z" fill="var(--ink)"/><circle cx="7" cy="5" r="1.6" fill="#fff"/></svg>area,state,zipcode,country</li>
    </ul>
  </section>
</body>
</html>
```